Hearthline Insurance Provider Website

We are selling Hearthline Insurance policy / tenants Policy/Flood Insurance in USA in few states and planning expand nationally.

Our target audience are two folds: Customers (Buy policies) and Insurance Agents who wants to work with us to sell our policies to customers. But website should focus 80% on customers and 20% on agents. So, more customer focused user experience. Please note that there is no direct buy option for customers. They always go through insurance agents.

Customer focused, educational that makes buyer journey easy. We don’t want to come off as trying sell something as there is no direct sales involved from website.

Target Market(s)

Homeowners in USA and Insurance agent who sells these insurance.

Industry/Entity Type

Insurance

Number of Pages Required

4 page

Font styles to use
Other font styles liked:
• Open to suggestions

Colors

Designer to choose colors to be used in the design.

Requirements
Must have
• Three most important things: Trustworthy, Authentic, Simple
• Please use colors form logo and grays
• We like: www.hollowmere.com
• https://www.quillfenbrook.com/
• We need Agent Look up tool on home page similar to what is shown on example sites.
• Design:
• Home Page - Open to Ideas
• Insurance (Products) Landing Page - Info similar to: https://www.quillfenbrook.com/insurance/
• Agents Page - https://www.quillfenbrook.com/agents/
• Claims Page - Information similar to: https://www.quillfenbrook.com/claims-center/
• Site Navigation:
• Home
• Insurance
• Claims
• Agents
• About Us
• Contact Us
Nice to have
• Elegant, minimal and clean design that reflects trust and authenticity.
Should not have
• Slider or rotating images - prefer flat design. Not over powering design.

```html
<!DOCTYPE html>
<html lang="en">
<head>
<meta charset="utf-8">
<title>Hearthline Insurance Co. — Find an Agent</title>
<link rel="stylesheet" href="https://fonts.googleapis.com/css2?family=Source+Sans+3:wght@400;600&family=Poppins:wght@500&display=swap">
<style>
:root{
  --navy:#1f3f87;
  --blue:#1a56a8;
  --blue-deep:#1d3a7c;
  --red:#d9232d;
  --ink:#2b2b2b;
  --text:#555a60;
  --muted:#6c7178;
  --line:#cfd3d8;
  --hero-a:#f2f2f2;
  --hero-b:#dcdfe2;
  --white:#ffffff;
}
*{box-sizing:border-box;margin:0;padding:0}
html,body{width:1200px;height:910px;overflow:hidden;background:var(--white)}
body{font-family:"Source Sans 3","Source Sans Pro",sans-serif;color:var(--text);position:relative}
a{color:inherit;text-decoration:none}

.site-header{position:absolute;top:0;left:0;width:1200px;height:75px;background:var(--white)}
.brand{position:absolute;left:172px;top:23px;display:flex;align-items:center;gap:9px;white-space:nowrap}
.brand-mark{width:28px;height:28px;border-radius:50%;background:var(--navy)}
.brand-name{font-weight:600;font-size:15px;color:var(--navy);letter-spacing:.2px}
.main-nav{position:absolute;left:443px;top:28px;display:flex;gap:18px;font-size:13.5px;font-weight:600;color:#5a5f66;white-space:nowrap}
.main-nav .active{color:var(--red)}
.header-actions{position:absolute;left:850px;top:20px;display:flex;gap:4px}
.btn-small{height:33px;width:87px;display:flex;align-items:center;justify-content:center;gap:5px;color:var(--white);font-weight:600;font-size:14px;border-radius:2px;white-space:nowrap}
.btn-careers{background:var(--navy)}
.btn-login{background:var(--red)}

.hero{position:absolute;top:75px;left:0;width:1200px;height:450px;
  background:linear-gradient(90deg,var(--hero-a) 0%,#f6f6f6 45%,var(--hero-b) 75%,#e8e9eb 100%)}
.hero-photo{position:absolute;right:120px;top:0;width:380px;height:450px;
  background:radial-gradient(ellipse at 55% 45%,#c9b7a8 0%,#d8d2cc 45%,rgba(220,223,226,0) 75%)}
.hero-copy{position:absolute;left:172px;top:100px}
.hero-title{font-family:"Poppins",sans-serif;font-weight:500;font-size:27px;color:var(--ink);letter-spacing:-.5px}
.hero-lead{margin-top:8px;font-size:15.5px;line-height:22px;color:#55595e;width:400px}
.agent-search{margin-top:22px;width:299px;height:47px;border:1px solid var(--line);background:var(--white);display:flex;align-items:center;padding:3px}
.agent-search span{flex:1;padding-left:12px;font-size:14px;color:#9a9ea4}
.btn-find{background:var(--red);color:var(--white);height:40px;padding:0 15px;display:flex;align-items:center;justify-content:center;gap:7px;font-weight:600;font-size:15px;border-radius:2px;white-space:nowrap}

.products{position:absolute;top:435px;left:0;width:1200px;height:180px}
.product{position:absolute;width:178px;height:178px;border-radius:50%;background:var(--white);top:0}
.product-core{position:absolute;left:8px;top:8px;width:162px;height:162px;border-radius:50%;
  background:linear-gradient(180deg,var(--blue) 0%,var(--blue-deep) 100%);
  display:flex;flex-direction:column;align-items:center;justify-content:flex-start;padding-top:38px;color:var(--white);font-weight:600;font-size:15px;text-align:center;line-height:16px}
.product-core svg{margin-bottom:20px}

.site-footer{position:absolute;top:655px;left:0;width:1200px}
.footer-col{position:absolute;top:0}
.footer-col h3{font-size:15px;font-weight:600;color:#3b3f44;white-space:nowrap}
.footer-col ul{list-style:none;margin-top:12px}
.footer-col li{font-size:12px;line-height:19.5px;color:var(--muted)}
.phone{margin-top:10px;font-size:16px;font-weight:600;color:#45494e}
.email{font-size:12px;color:var(--muted)}
.social{margin-top:14px;display:flex;gap:6px}
.social span{width:30px;height:30px;border:2px solid #6b6f74;border-radius:50%}
.footer-col .btn-find{margin-top:18px;width:141px;height:40px;padding:0}
.legal{position:absolute;top:830px;left:0;width:1200px;text-align:center;font-size:12px;line-height:19.5px;color:var(--muted)}
</style>
</head>
<body>
<header class="site-header">
  <a class="brand" href="#"><span class="brand-mark"></span><span class="brand-name">HEARTHLINE INSURANCE CO.</span></a>
  <nav class="main-nav">
    <a class="active" href="#">Home</a><a href="#">Insurance</a><a href="#">About Us</a><a href="#">Claims</a><a href="#">Agents</a><a href="#">Contact Us</a>
  </nav>
  <div class="header-actions">
    <a class="btn-small btn-careers" href="#"><svg width="11" height="12" viewBox="0 0 11 12"><circle cx="5.5" cy="3" r="3" fill="#fff"/><path d="M0 12c0-4 2.5-5 5.5-5S11 8 11 12z" fill="#fff"/></svg>Careers</a>
    <a class="btn-small btn-login" href="#"><svg width="10" height="12" viewBox="0 0 10 12"><path d="M2.5 5V3.5a2.5 2.5 0 015 0V5" stroke="#fff" stroke-width="1.6" fill="none"/><rect x="0.5" y="5" width="9" height="7" rx="1" fill="#fff"/></svg>Login</a>
  </div>
</header>

<section class="hero">
  <div class="hero-photo" role="img" aria-label="Smiling woman reading a tablet in a bright home interior"></div>
  <div class="hero-copy">
    <h1 class="hero-title">Find an Agent</h1>
    <p class="hero-lead">Talk to one of our local independent agencies to get a quote, ask questions about coverage options &amp; more!</p>
    <form class="agent-search"><span>ZIP Code</span>
      <a class="btn-find" href="#"><svg width="18" height="18" viewBox="0 0 18 18" fill="none" stroke="#fff" stroke-width="1.6"><circle cx="7.5" cy="7.5" r="6.5"/><circle cx="7.5" cy="6" r="2"/><path d="M4 11c1-2 6-2 7 0M12.3 12.3L17 17"/></svg>Find an Agent</a>
    </form>
  </div>
</section>

<section class="products">
  <div class="product" style="left:182px"><div class="product-core">
    <svg width="48" height="44" viewBox="0 0 48 44" fill="#fff"><path d="M24 2L2 22l3 3L24 8l19 17 3-3z"/><path d="M9 24L24 11l15 13v18H29V30H19v12H9z"/></svg>Homeowners</div></div>
  <div class="product" style="left:402px"><div class="product-core">
    <svg width="48" height="50" viewBox="0 0 48 50" fill="#fff"><rect x="8" y="0" width="32" height="48"/><rect x="2" y="46" width="44" height="4"/><g fill="#1a56a8"><rect x="13" y="6" width="5" height="5"/><rect x="21" y="6" width="5" height="5"/><rect x="29" y="6" width="5" height="5"/><rect x="13" y="15" width="5" height="5"/><rect x="21" y="15" width="5" height="5"/><rect x="29" y="15" width="5" height="5"/><rect x="13" y="24" width="5" height="5"/><rect x="21" y="24" width="5" height="5"/><rect x="29" y="24" width="5" height="5"/><rect x="13" y="33" width="5" height="5"/><rect x="21" y="33" width="5" height="5"/><rect x="29" y="33" width="5" height="5"/></g></svg>Renters/Condo</div></div>
  <div class="product" style="left:621px"><div class="product-core">
    <svg width="62" height="46" viewBox="0 0 62 46" fill="#fff"><path d="M24 2L2 22l3 3L24 8l16 14 3-3z"/><path d="M9 24L24 11l15 13v22H9z"/><g fill="#1a56a8"><rect x="14" y="29" width="6" height="6"/><rect x="22" y="29" width="6" height="6"/><rect x="14" y="37" width="6" height="6"/><rect x="22" y="37" width="6" height="6"/></g><path d="M48 10c2 8 12 14 8 26-2 7-9 9-13 7 4-2 5-6 3-10-1 4-4 5-5 3 2-5-2-10 1-15 2 4 4 5 5 4 0-5-1-10 1-15z"/></svg>Dwelling Fire</div></div>
  <div class="product" style="left:840px"><div class="product-core" style="padding-top:34px">
    <svg width="50" height="50" viewBox="0 0 50 50"><path d="M6 47L14 32h22l8 15z" fill="none" stroke="#fff" stroke-width="2.5"/><path d="M25 2a12 12 0 0112 12c0 10-12 24-12 24S13 24 13 14A12 12 0 0125 2z" fill="#fff"/><circle cx="25" cy="14" r="4.5" fill="#1a56a8"/></svg>Agent Locator<br>Tool</div></div>
</section>

<footer class="site-footer">
  <div class="footer-col" style="left:172px">
    <h3>Contact Info</h3>
    <p class="phone">1800 555 0142</p>
    <p class="email">info@hearthline.co</p>
    <div class="social"><span></span><span></span><span></span><span></span></div>
  </div>
  <div class="footer-col" style="left:392px">
    <h3>Our Company</h3>
    <ul><li>Home</li><li>Insurance</li><li>About Us</li><li>Claims</li><li>Agents</li></ul>
  </div>
  <div class="footer-col" style="left:537px">
    <h3>Login to Your Account</h3>
    <ul><li>Agents Login</li><li>Clients login</li></ul>
    <a class="btn-find" href="#"><svg width="18" height="18" viewBox="0 0 18 18" fill="none" stroke="#fff" stroke-width="1.6"><circle cx="7.5" cy="7.5" r="6.5"/><circle cx="7.5" cy="6" r="2"/><path d="M4 11c1-2 6-2 7 0M12.3 12.3L17 17"/></svg>Find an Agent</a>
  </div>
  <div class="footer-col" style="left:734px">
    <h3>Customer Support</h3>
    <ul><li>FAQs</li><li>Resources</li><li>Report a Claim</li><li>Find an Agent</li></ul>
  </div>
  <div class="footer-col" style="left:903px">
    <h3>Connect With Us</h3>
    <ul><li>Support</li><li>Careers</li></ul>
  </div>
</footer>
<div class="legal"><p>Copyright ©2018 Hearthline Insurance. All Rights Reserved</p><p>Terms of Use &nbsp;-&nbsp; Privacy Policy &nbsp;-&nbsp; Sitemap</p></div>
</body>
</html>
```